Brell Stone Company Business Cards

Front and Back Business Card - logo and text setup - cool design. I need workable photoshop or illustrator files so I can setup each employee card with design that is created
Updates

Hi everyone, thank you for the great entries. Please no more white and blue cards - there are so many already - black and silver only now please. thanks!

Target Market(s)

Construction Industry - Facility Managers

Industry/Entity Type

Construction

Contact Information for Business Card

I really like contemporary simplistic looks - clean neat....not opposed to seeing some black backrounds

Requirements
Must have
• Logo/website address with design on front only - www.brellstone-example.com (logo attached)
• Back:
• Name/Title/Company Address/Phone/email address
Nice to have
• Cool design
Should not have
• Nothing gimmicky like Fire or Water - since we are a Fire Protection company - it has all been done

```html
<!DOCTYPE html>
<html lang="en">
<head>
<meta charset="UTF-8">
<title>Brell Stone Company Business Cards</title>
<link href="https://fonts.googleapis.com/css2?family=Poppins:wght@400;500;600;700&display=swap" rel="stylesheet">
<style>
  :root {
    --page-bg: #ecebe8;
    --black: #141414;
    --front-black: #1a1a1b;
    --front-mark: #2c2d2f;
    --silver: #b9bcc1;
    --silver-light: #e4e6e9;
    --silver-mid: #cfd2d6;
    --text-dark: #3a3c40;
  }
  * { margin: 0; padding: 0; box-sizing: border-box; }
  html, body { width: 1200px; height: 920px; overflow: hidden; }
  body {
    background: var(--page-bg);
    font-family: "Poppins", Arial, sans-serif;
    position: relative;
  }
  .card {
    position: absolute;
    top: 310px;
    width: 535px;
    height: 300px;
    box-shadow: 0 6px 18px rgba(0,0,0,0.22);
  }
  /* Front */
  .card-front {
    left: 45px;
    background: var(--front-black);
  }
  .front-name {
    position: absolute;
    left: 0; right: 0;
    top: 108px;
    text-align: center;
    font-size: 60px;
    font-weight: 700;
    letter-spacing: -1px;
    color: var(--front-mark);
    line-height: 1;
  }
  .front-web {
    position: absolute;
    left: 0; right: 0;
    bottom: 26px;
    text-align: center;
    font-size: 14px;
    letter-spacing: 1px;
    color: #ffffff;
  }
  .front-web .web-accent { color: var(--silver); }
  /* Back */
  .card-back {
    left: 620px;
    background: linear-gradient(135deg, var(--silver-light) 0%, var(--silver-mid) 100%);
  }
  .person {
    position: absolute;
    left: 62px;
    top: 90px;
  }
  .person-name {
    font-size: 18px;
    font-weight: 600;
    color: var(--black);
    letter-spacing: 0.5px;
  }
  .person-title {
    font-size: 11px;
    color: var(--text-dark);
    margin-top: 2px;
  }
  .company-name {
    position: absolute;
    right: 62px;
    top: 84px;
    font-size: 40px;
    font-weight: 700;
    letter-spacing: -1px;
    color: var(--black);
    line-height: 1;
  }
  .divider {
    position: absolute;
    left: 62px;
    right: 62px;
    top: 150px;
    height: 1.5px;
    background: var(--black);
  }
  .contact-list {
    position: absolute;
    left: 62px;
    top: 170px;
    list-style: none;
  }
  .contact-list li {
    display: flex;
    align-items: center;
    gap: 9px;
    font-size: 13px;
    color: var(--text-dark);
    height: 19px;
  }
  .contact-list svg { width: 10px; height: 10px; flex: none; }
  .address {
    position: absolute;
    left: 310px;
    top: 172px;
    font-size: 12.5px;
    color: var(--text-dark);
    line-height: 19px;
  }
  .address-company {
    font-size: 10px;
    font-weight: 600;
    color: var(--black);
  }
</style>
</head>
<body>

<section class="card card-front" aria-label="Card front">
  <div class="front-name">brellstone</div>
  <div class="front-web">www.<span class="web-accent">brellstone-example</span>.com</div>
</section>

<section class="card card-back" aria-label="Card back">
  <div class="person">
    <div class="person-name">DANA WHITFIELD</div>
    <div class="person-title">Senior Consultant</div>
  </div>
  <div class="company-name">brellstone</div>
  <div class="divider"></div>

  <ul class="contact-list">
    <li>
      <svg viewBox="0 0 10 10" aria-hidden="true"><path d="M2 0.8 L3.6 2.6 L2.7 3.7 Q3.8 5.9 6.3 7.3 L7.4 6.4 L9.2 8 L8 9.4 Q4.5 9.3 2.2 6.6 Q0.4 4.4 0.7 2 Z" fill="var(--black)"/></svg>
      (555) 014-2210
    </li>
    <li>
      <svg viewBox="0 0 10 10" aria-hidden="true"><rect x="2.5" y="0.8" width="5" height="2.4" fill="none" stroke="var(--black)" stroke-width="1"/><rect x="0.8" y="3.2" width="8.4" height="4" rx="0.6" fill="var(--black)"/><rect x="2.5" y="6" width="5" height="3.2" fill="var(--silver-light)" stroke="var(--black)" stroke-width="1"/></svg>
      (555) 014-2211
    </li>
    <li>
      <svg viewBox="0 0 10 10" aria-hidden="true"><rect x="0.8" y="2" width="8.4" height="6" fill="none" stroke="var(--black)" stroke-width="1"/><path d="M0.8 2 L5 5.5 L9.2 2" fill="none" stroke="var(--black)" stroke-width="1"/></svg>
      info@brellstone-example.com
    </li>
    <li>
      <svg viewBox="0 0 10 10" aria-hidden="true"><circle cx="5" cy="5" r="4.2" fill="none" stroke="var(--black)" stroke-width="1"/><ellipse cx="5" cy="5" rx="1.8" ry="4.2" fill="none" stroke="var(--black)" stroke-width="0.8"/><path d="M0.8 5 H9.2" stroke="var(--black)" stroke-width="0.8"/></svg>
      www.brellstone-example.com
    </li>
  </ul>

  <div class="address">
    <div class="address-company">brellstone inc.</div>
    <div>48 Harbor Point</div>
    <div>Drive East Lindale, NY 10040</div>
  </div>
</section>

</body>
</html>
```